Association qui souhaite améliorer l'accès aux personnes en situation de handicap

Nous sommes une association qui a pour objectif d'améliorer l'accessibilité, augmenter l'offre des activités réalisables dans notre région touristique.
Nous souhaitons réaliser un site internet afin de pouvoir communiquer sur notre association. Nous avons déjà conçu notre flyer sur Plumotrix. Nous souhaiterions une base graphique se rapportant à celui-ci. C'est possible de tout retravailler mais nous souhaitons tout de même retrouver la charte graphique ou code couleur du flyer.
Il nous faudrait quelques pages:
- 1 page : Acceuil / Présentation (Home), Il y aurait le descriptif de l'association, avec ses objectifs à +/- moyen terme
- 1 page : Nos réalisations, celle-ci présenterait les éléments que nous avons réalisés avec des zones de textes et des images classées chronologiquement au fur et à mesure des nouveautés
- 1 page : Media, comme la précédente, mais ou on pourrait voir ou lire sur les divers médias qui parlent de nous
- 1 page : Evenements : c'est une page pour présenter divers activités que nous allons organiser
- 1 page : Contact qui indique comment nous contacter et avec la présentation des 5 ou 6 membres du comité
- 1 link donate : qui arrive sur un formulaire de donnée que l'on pourra faire évoluer sur un système de payement par la suite. Cette bannière doit se retrouver sur toutes les pages
Il est nécessaire que se design puisse être transféré sur une lecture sur téléphone mobile
Personnes en situation de handicap
Associatif

```html
<!DOCTYPE html>
<html lang="en">
<head>
<meta charset="utf-8">
<title>OpenPath Association – Events</title>
<link href="https://fonts.googleapis.com/css2?family=Raleway:wght@400;500;600;700;800&family=Bebas+Neue&display=swap" rel="stylesheet">
<style>
:root{
  --red:#c0192a;
  --bright-red:#e8232f;
  --ink:#1d1d1d;
  --text:#333;
  --muted:#8a8a8a;
  --link:#2a5bb8;
  --dark:#272e31;
  --line:#e3e3e3;
  --white:#fff;
}
*{box-sizing:border-box;margin:0;padding:0}
html,body{width:1200px;height:2531px;overflow:hidden}
body{position:relative;font-family:"Raleway",sans-serif;color:var(--text);background:var(--white)}
.abs{position:absolute}
.topbar{left:0;top:0;width:1200px;height:29px;background:var(--red);color:var(--white);font-size:11px}
.topbar .social{left:130px;top:9px;width:10px;height:10px;border-radius:50%;background:var(--white)}
.topbar .mail{right:128px;top:8px;display:flex;align-items:center;gap:6px;font-weight:500}
.header{left:0;top:29px;width:1200px;height:61px;background:var(--white);border-bottom:1px solid #eee}
.brand{left:130px;top:22px;display:flex;align-items:center;gap:8px}
.brand .dot{width:14px;height:14px;background:var(--red)}
.brand span{font-weight:800;font-size:15px;color:var(--ink);letter-spacing:.2px}
.nav{left:538px;top:24px;display:flex;gap:41px;font-size:11px;font-weight:500;color:var(--ink)}
.nav .active{color:var(--red);position:relative}
.nav .active svg{position:absolute;left:2px;top:15px}
.donate{left:976px;top:15px;width:95px;height:30px;border-radius:15px;background:var(--red);color:var(--white);font-size:11px;font-weight:700;display:flex;align-items:center;justify-content:center}
.hero{left:0;top:90px;width:1200px;height:273px;background:linear-gradient(100deg,#5a5a5a 0%,#7a6f6a 35%,#6e7a86 65%,#8b8c8f 100%)}
.hero-shade{left:0;top:90px;width:1200px;height:273px;background:rgba(0,0,0,.28)}
.hero-title{left:0;top:194px;width:1200px;text-align:center;font-size:34px;font-weight:800;color:var(--white);letter-spacing:.5px;line-height:40px}
.hero-title em{font-style:normal;color:var(--bright-red)}
.crumb{left:0;top:241px;width:1200px;text-align:center;font-size:10px;color:var(--white)}
.crumb span{color:#ddd}
.section-title{left:128px;top:422px;font-size:34px;font-weight:500;color:var(--ink)}
.section-intro{left:129px;top:473px;width:480px;font-size:13px;line-height:20px;font-weight:500;color:var(--ink)}
.event{left:130px;width:620px}
.event .photo{width:620px;height:291px}
.event h2{margin-top:33px;font-size:19px;font-weight:500;color:var(--ink)}
.event .date{margin-top:12px;font-size:11px;color:#555}
.event p{margin-top:23px;padding-left:2px;font-size:12px;line-height:20.5px;color:var(--ink);font-weight:500}
.sidebar{left:829px;top:535px;width:241px}
.sidebar h3{font-size:17px;font-weight:500;color:var(--ink)}
.post{display:flex;gap:20px;margin-top:20px}
.post .thumb{width:81px;height:62px;flex:none}
.post h4{font-size:10px;font-weight:500;color:var(--link);margin-top:2px}
.post p{font-size:8.5px;line-height:12.5px;color:#555;margin-top:6px}
.post small{display:block;font-size:7px;color:var(--muted);margin-top:6px}
.divider{height:1px;background:var(--line);margin:20px 0 18px}
.email-input{margin-top:20px;height:34px;border:1px solid #ddd;font-size:9px;color:#444;padding:11px 11px}
.subscribe{margin-top:8px;height:34px;background:#111;color:var(--white);font-size:10px;display:flex;align-items:center;justify-content:center;font-weight:500}
.footer-bg{left:0;top:2107px;width:1200px;height:424px}
.f-brand{left:130px;top:2290px;display:flex;align-items:center;gap:8px}
.f-brand .dot{width:16px;height:16px;background:var(--white)}
.f-brand span{font-weight:800;font-size:16px;color:var(--white)}
.f-about{left:130px;top:2342px;width:210px;font-size:10px;line-height:16px;color:var(--white)}
.f-social{left:130px;top:2404px;width:22px;height:22px;border-radius:50%;background:var(--red)}
.f-col{top:2270px;color:var(--white)}
.f-col h5{font-family:"Bebas Neue",sans-serif;font-weight:400;font-size:20px;color:var(--bright-red);letter-spacing:.3px}
.f-col ul{list-style:none;margin-top:6px}
.f-col li{font-size:10.5px;line-height:23px}
.contact-row{display:flex;gap:8px;align-items:center;margin-top:10px;font-size:10.5px;line-height:14px}
.contact-row .ic{width:22px;height:22px;border-radius:50%;border:1px solid var(--white);display:flex;align-items:center;justify-content:center;flex:none}
.f-rule{left:130px;top:2484px;width:940px;border-top:1px dotted #4a5357}
.copyright{left:0;top:2508px;width:1200px;text-align:center;font-size:10px;color:var(--white)}
.copyright span{color:var(--bright-red)}
</style>
</head>
<body>

<div class="abs topbar">
  <div class="abs social"></div>
  <div class="abs mail">
    <svg width="12" height="9" viewBox="0 0 12 9"><rect x=".5" y=".5" width="11" height="8" fill="none" stroke="#fff"/><path d="M.5 .5 6 5l5.5-4.5" fill="none" stroke="#fff"/></svg>
    info@openpath-association.org
  </div>
</div>

<header class="abs header">
  <div class="abs brand"><div class="dot"></div><span>OpenPath Association</span></div>
  <nav class="abs nav">
    <span>Home</span><span>Our Achievements</span><span>Media</span>
    <span class="active">Events<svg width="30" height="8" viewBox="0 0 30 8"><path d="M0 1l5 5 5-5 5 5 5-5 5 5 5-5" fill="none" stroke="#c0192a" stroke-width="1.4"/></svg></span>
    <span>Contacts</span>
  </nav>
  <div class="abs donate">DONATE</div>
</header>

<div class="abs hero" role="img" aria-label="Smiling woman in a wheelchair holding a coloured smoke flare in front of a wooden wall"></div>
<div class="abs hero-shade"></div>
<h1 class="abs hero-title">OUR <em>EVENT</em></h1>
<div class="abs crumb"><span>Home</span> | Event</div>

<h2 class="abs section-title">Recent Event</h2>
<p class="abs section-intro">Sed ut perspiciatis unde omnis iste natus error sit voluptatem accusantium doloremque laudantium</p>

<article class="abs event" style="top:540px">
  <div class="photo" role="img" aria-label="Patients in wheelchairs gathered on a hospital terrace with plants" style="background:linear-gradient(120deg,#cfd3d6,#6f7a7e 45%,#2f3a44)"></div>
  <h2>Excepteur sint occaecat cupidatat non proident Sunt in Culpa</h2>
  <div class="date">Online on March 30, 2022</div>
  <p>Sed ut perspiciatis unde omnis iste natus error sit voluptatem accusantium doloremque laudantium, totam rem aperiam, eaque ipsa quae ab illo inventore veritatis et quasi architecto beatae vitae dicta sunt explicabo.&nbsp; Nemo enim ipsam voluptatem quia voluptas sit aspernatur aut odit aut fugit, sed quia consequuntur magni dolores eos qui ratione voluptatem sequi nesciunt.</p>
</article>

<article class="abs event" style="top:1070px">
  <div class="photo" role="img" aria-label="Man in a red shirt beside an adapted mountain vehicle on green alpine slopes" style="background:linear-gradient(110deg,#b9bfbd,#8c9b6a 40%,#6e8a4a 70%,#98a77c)"></div>
  <h2>Excepteur sint occaecat cupidatat non proident Sunt in Culpa</h2>
  <div class="date">Online on March 30, 2022</div>
  <p>Sed ut perspiciatis unde omnis iste natus error sit voluptatem accusantium doloremque laudantium, totam rem aperiam, eaque ipsa quae ab illo inventore veritatis et quasi architecto beatae vitae dicta sunt explicabo.&nbsp; Nemo enim ipsam voluptatem quia voluptas sit aspernatur aut odit aut fugit, sed quia consequuntur magni dolores eos qui ratione voluptatem sequi nesciunt.</p>
</article>

<article class="abs event" style="top:1599px">
  <div class="photo" role="img" aria-label="Large group of people dressed in red Santa costumes posing indoors" style="background:linear-gradient(180deg,#5a4a3e,#b8282c 45%,#c9302f 75%,#8a2a2a)"></div>
  <h2>Excepteur sint occaecat cupidatat non proident Sunt in Culpa</h2>
  <div class="date">Online on March 30, 2022</div>
  <p>Sed ut perspiciatis unde omnis iste natus error sit voluptatem accusantium doloremque laudantium, totam rem aperiam, eaque ipsa quae ab illo inventore veritatis et quasi architecto beatae vitae dicta sunt explicabo.&nbsp; Nemo enim ipsam voluptatem quia voluptas sit aspernatur aut odit aut fugit, sed quia consequuntur magni dolores eos qui ratione voluptatem sequi nesciunt.</p>
</article>

<aside class="abs sidebar">
  <h3>News</h3>
  <div class="post">
    <div class="thumb" role="img" aria-label="Wheelchair athletes on a sports court" style="background:linear-gradient(135deg,#8a9aa8,#3e4e7a)"></div>
    <div><h4>Casa Marlena</h4><p>Her name is Marlena. She fell in love with Colombia and for the markets that she visits...</p><small>Online on March 30, 2022</small></div>
  </div>
  <div class="post" style="margin-top:26px">
    <div class="thumb" role="img" aria-label="Child blowing dandelion seeds in a meadow" style="background:linear-gradient(135deg,#5fa84a,#3d4a8a)"></div>
    <div><h4>Casa Marlena</h4><p>Her name is Marlena. She fell in love with Colombia and for the markets that she visits...</p><small>Online on March 30, 2022</small></div>
  </div>
  <div class="divider"></div>
  <h3>Press Articles</h3>
  <div class="post">
    <div class="thumb" role="img" aria-label="Two hands reaching out over grass" style="background:linear-gradient(135deg,#9aa57a,#c9b8a0 50%,#4a5a3a)"></div>
    <div><h4>Casa Marlena</h4><p>Her name is Marlena. She fell in love with Colombia and for the markets that she visits...</p><small>Online on March 30, 2022</small></div>
  </div>
  <div class="divider"></div>
  <h3>Newsletter</h3>
  <div class="email-input">Enter Your email:</div>
  <div class="subscribe">SUBSCRIBE</div>
</aside>

<svg class="abs footer-bg" viewBox="0 0 1200 424" preserveAspectRatio="none">
  <polygon points="0,53 472,130 1200,0 1200,424 0,424" fill="#272e31"/>
</svg>

<div class="abs f-brand"><div class="dot"></div><span>OpenPath Association</span></div>
<p class="abs f-about">Sed ut perspiciatis unde omnis iste natus error sit voluptatem accusantium rem aperiam</p>
<div class="abs f-social"></div>

<div class="abs f-col" style="left:450px">
  <h5>SITEMAP</h5>
  <ul><li>Home</li><li>Our Achivements</li><li>Media</li><li>Events</li><li>Contact Us</li></ul>
</div>
<div class="abs f-col" style="left:670px">
  <h5>OTHERS</h5>
  <ul><li>Privacy Policy</li><li>Terms &amp; Conditions</li><li>Leagal</li><li>Donate</li><li>Help / Support</li></ul>
</div>
<div class="abs f-col" style="left:876px;width:200px">
  <h5>CONTACTS</h5>
  <div class="contact-row">
    <div class="ic"><svg width="8" height="11" viewBox="0 0 8 11"><path d="M4 10.5S.5 6.5.5 4a3.5 3.5 0 0 1 7 0c0 2.5-3.5 6.5-3.5 6.5z" fill="#e8232f"/><circle cx="4" cy="4" r="1.2" fill="#272e31"/></svg></div>
    <span>Chemin des Alpes 12 / 1900<br>Valmont</span>
  </div>
  <div class="contact-row">
    <div class="ic"><svg width="11" height="8" viewBox="0 0 11 8"><rect width="11" height="8" fill="#e8232f"/><path d="M0 0l5.5 4.5L11 0" fill="none" stroke="#272e31"/></svg></div>
    <span>info@openpath-association.org</span>
  </div>
</div>

<div class="abs f-rule"></div>
<div class="abs copyright">Copyright © 2022 <span>OpenPath Association</span>. All Rights Reserved.</div>

</body>
</html>
```